Alloy wheel repair business needs a website

Install logo previously purchased from makerhive, toolbar with dropdowns. services, gallery, clients , contact ect
Maybe mission statment

Target Market(s)

vehicle owners, auto dealers,insurance companies,

Industry/Entity Type

Alloy Wheel Repair

Coding

Coded - Design and coding required

Number of Pages Required

4 page

Font styles to use
Sans Serif

Colors
0054AA
0677BA
7BADD7
CADEEF
E8F1F8

```html
<!DOCTYPE html>
<html lang="en">
<head>
<meta charset="utf-8">
<title>Kestrel Rimcare – Alloy Wheel Repair</title>
<link rel="stylesheet" href="https://fonts.googleapis.com/css2?family=Russo+One&family=Roboto:ital,wght@0,400;0,500;0,700;1,400&display=swap">
<style>
:root{
  --blue:#0054AA;--blue2:#0677BA;--blue3:#3F86C9;--sky:#7BADD7;--pale:#CADEEF;--mist:#E8F1F8;
  --navy:#06244F;--navy2:#0A3A73;--ink:#111318;--dark:#17191D;--grey:#F1F1F1;--text:#4A4F57;--white:#fff;
}
*{box-sizing:border-box;margin:0;padding:0}
html,body{width:1200px;height:5121px;overflow:hidden}
body{font-family:"Roboto",sans-serif;color:var(--ink);background:var(--grey);position:relative}
.section{position:absolute;left:0;width:1200px}
.display{font-family:"Russo One",sans-serif;font-style:italic;letter-spacing:3px;text-transform:uppercase;line-height:1.05}
.eyebrow{font-weight:500;letter-spacing:5px;text-transform:uppercase;font-size:21px}
.center{text-align:center}
.btn{display:inline-block;font-family:"Russo One",sans-serif;font-size:12px;letter-spacing:2px;text-transform:uppercase;color:#fff;background:var(--blue3);padding:12px 24px;box-shadow:0 0 0 3px rgba(63,134,201,.35)}
.btn.outline{background:transparent;border:1px solid #fff;box-shadow:none}
.photo{position:absolute}
.brand{font-family:"Roboto",sans-serif;font-weight:700;text-transform:uppercase;letter-spacing:3px;line-height:1;display:flex;align-items:center;gap:10px}
.brand .dot{width:14px;height:14px;border-radius:50%;background:currentColor;flex:none}

.header{top:0;height:100px;background:#fff}
.header .brand{position:absolute;left:122px;top:26px;color:var(--blue3);font-size:22px}
.nav{position:absolute;left:486px;top:40px;display:flex;gap:30px;font-size:13px;font-weight:500}
.call{position:absolute;left:944px;top:26px;display:flex;gap:10px;align-items:center}
.call small{display:block;font-size:11px}
.call b{font-size:16px}

.hero{top:100px;height:508px;background:#000}
.hero .photo{left:520px;top:0;width:680px;height:508px;background:radial-gradient(circle at 60% 50%,#8a8f96 0,#3b3e44 35%,#111 75%)}
.hero .eyebrow{position:absolute;left:122px;top:112px;color:#fff;font-size:21px}
.hero .brand-big{position:absolute;left:122px;top:150px;color:#fff;font-size:58px;font-weight:700;letter-spacing:6px;line-height:1.1;text-transform:uppercase}
.hero .tag{position:absolute;left:118px;top:312px;color:#fff;font-size:18px;font-weight:500;letter-spacing:1px}
.hero .btn{position:absolute;left:118px;top:378px}

.services{top:608px;height:714px;background:linear-gradient(180deg,#fff 0,#eeeeee 100%)}
.services .eyebrow{position:absolute;top:96px;width:100%;color:var(--blue3)}
.services h2{position:absolute;top:138px;width:100%;font-size:48px}
.card{position:absolute;top:212px;width:272px;height:328px;background:#fff;box-shadow:0 6px 24px rgba(0,0,0,.08);text-align:center;padding:24px 24px 0}
.card.active{background:var(--navy);color:#fff;box-shadow:0 10px 30px rgba(6,36,79,.5)}
.card .icon{display:block;width:64px;height:64px;margin:0 auto 16px}
.card h3{font-size:17px;font-weight:500;letter-spacing:1.5px;line-height:1.5;text-transform:uppercase}
.card p{font-size:12.5px;line-height:1.65;letter-spacing:.5px;color:var(--text);margin-top:14px}
.card.active p{color:#d7e3f2}
.card .more{position:absolute;left:0;right:0;bottom:22px;font-size:12px;font-weight:500;letter-spacing:1px;color:var(--blue3)}
.card.active .more{color:var(--sky)}
.services .btn{position:absolute;left:496px;top:584px}

.mission{top:1322px;height:576px;background:linear-gradient(90deg,var(--navy) 0,var(--navy2) 100%)}
.mission .eyebrow{position:absolute;top:78px;width:100%;color:#fff}
.mission h2{position:absolute;top:120px;width:100%;color:#fff;font-size:46px}
.point{position:absolute;top:218px;width:420px;color:#fff}
.point .tick{position:absolute;left:0;top:0;width:56px;height:56px;background:var(--blue3);display:flex;align-items:center;justify-content:center}
.point h4{margin-left:79px;font-size:18px;font-weight:500;letter-spacing:2px}
.point p{margin-left:79px;margin-top:22px;font-size:12.5px;line-height:1.75;color:#dfe7f2}
.mission-photo{top:1737px;left:159px;width:878px;height:397px;border-radius:16px;background:linear-gradient(90deg,#25272b 0,#6d7076 45%,#b5b8bc 55%,#2e3035 100%);border:3px solid #fff;box-shadow:0 20px 40px rgba(0,0,0,.25)}

.gallery-head .eyebrow{position:absolute;top:2260px;width:100%;color:var(--blue3)}
.gallery-head h2{position:absolute;top:2296px;width:100%;font-size:46px}
.tile{position:absolute;width:280px;height:266px;background:linear-gradient(145deg,#5d6168,#2a2c31)}
.view-all{position:absolute;top:2984px;left:544px;font-family:"Russo One",sans-serif;font-style:italic;font-size:13px;letter-spacing:2px;color:var(--blue3);border-bottom:2px solid var(--blue3);padding-bottom:4px}

.quote{top:3086px;height:429px;background:linear-gradient(90deg,var(--navy) 0,var(--navy2) 100%);color:#fff}
.quote .eyebrow{position:absolute;top:66px;width:100%}
.quote h2{position:absolute;top:108px;width:100%;font-size:44px;line-height:1.22}
.quote .rule{position:absolute;left:570px;top:234px;width:60px;height:3px;background:var(--blue3)}
.quote p{position:absolute;top:254px;width:100%;font-size:17px;font-weight:500;line-height:1.6;letter-spacing:1px}
.quote .btns{position:absolute;top:336px;width:100%;display:flex;justify-content:center;gap:22px}

.testimonials{top:3515px;height:658px;background:#fff}
.testimonials .eyebrow{position:absolute;top:86px;width:100%;color:var(--blue3)}
.testimonials h2{position:absolute;top:124px;width:100%;font-size:46px}
.review{position:absolute;top:207px;width:272px;height:272px;background:#fff;box-shadow:0 6px 26px rgba(0,0,0,.1);padding:50px 26px 0}
.review.active{border:2px solid var(--blue3)}
.review .qm{position:absolute;left:24px;top:-16px;font-family:"Russo One",sans-serif;font-size:90px;color:var(--blue3);line-height:1}
.review p{font-size:12px;font-style:italic;line-height:1.75;color:var(--text)}
.who{position:absolute;top:510px;display:flex;gap:12px;align-items:center}
.who .av{width:40px;height:40px;border-radius:50%;background:linear-gradient(135deg,#6e5a4c,#2b2b2b)}
.who b{display:block;font-family:"Russo One",sans-serif;font-style:italic;font-size:13px;letter-spacing:2px}
.who span{color:#F2B705;font-size:16px;letter-spacing:2px}
.dots{position:absolute;top:592px;left:554px;display:flex;gap:6px}
.dots i{width:28px;height:4px;background:var(--pale)}
.dots i.on{background:var(--blue3)}

.contact{top:4173px;height:540px;background:linear-gradient(90deg,#2b2d31 0,#1c1e22 100%);color:#fff}
.contact .photo{left:0;top:0;width:616px;height:540px;background:linear-gradient(100deg,#55585d 0,#2f3236 60%,#1e2024 100%)}
.contact .eyebrow{position:absolute;left:640px;top:68px}
.contact h2{position:absolute;left:640px;top:106px;font-size:46px;line-height:1.15}
.field{position:absolute;border-bottom:1px solid #777;height:52px;font-size:13px;font-weight:500;letter-spacing:1px}
.field em{color:#e14b4b;font-style:normal}
.contact .btn{position:absolute;left:644px;top:454px}

.footer{top:4713px;height:408px;background:linear-gradient(135deg,#16181c,#0c0d10);color:#fff}
.footer .brand{position:absolute;left:104px;top:92px;color:#fff;font-size:26px}
.footer .about{position:absolute;left:108px;top:218px;width:300px;font-size:12px;line-height:1.6;color:#cfd3d8}
.socials{position:absolute;left:108px;top:262px;display:flex;gap:8px}
.socials i{width:26px;height:26px;border:1px solid #fff;border-radius:50%}
.col{position:absolute;top:90px}
.col h5{font-size:15px;font-weight:500;letter-spacing:2px;margin-bottom:26px}
.col li{list-style:none;font-size:13px;color:#a9aeb5;line-height:1.3;margin-bottom:16px;letter-spacing:.5px}
.col.contact-col li{display:flex;gap:10px}
.col svg{flex:none;margin-top:2px}
.footer .line{position:absolute;left:108px;top:352px;width:990px;height:1px;background:#3a3d42}
.footer .copy{position:absolute;top:374px;width:100%;font-size:13px;color:#cfd3d8}
</style>
</head>
<body>

<header class="section header">
  <div class="brand"><span class="dot"></span><span>Kestrel<br>Rimcare</span></div>
  <nav class="nav"><span>Services ▾</span><span>Gallery</span><span>Our Clients</span><span>Contact Us</span></nav>
  <div class="call">
    <svg width="28" height="28" viewBox="0 0 24 24" fill="none" stroke="#0677BA" stroke-width="2"><path d="M5 3h4l2 5-3 2a11 11 0 0 0 6 6l2-3 5 2v4a2 2 0 0 1-2 2A17 17 0 0 1 3 5a2 2 0 0 1 2-2z"/></svg>
    <div><small>Call Us!</small><b>(406) 555-0188</b></div>
  </div>
</header>

<section class="section hero">
  <div class="photo" role="img" aria-label="Photo of a car wheel mounted on a wheel alignment clamp"></div>
  <div class="eyebrow">Welcome to</div>
  <div class="brand-big">Kestrel<br>Rimcare</div>
  <div class="tag">Your Premier Alloy Wheel Repair Specialists</div>
  <a class="btn">Get a free quote</a>
</section>

<section class="section services">
  <div class="eyebrow center">Services</div>
  <h2 class="display center">What we do</h2>
  <div class="card" style="left:163px">
    <svg class="icon" viewBox="0 0 76 76" role="img" aria-label="Wheel rim icon" fill="none" stroke="#222" stroke-width="3"><circle cx="38" cy="38" r="34"/><circle cx="38" cy="38" r="8"/></svg>
    <h3>Wheel Rim<br>Refinishing</h3>
    <p>Restore damaged or corroded wheel rims to their original condition through sanding, filling, and painting.</p>
    <div class="more">REED MORE ⟶</div>
  </div>
  <div class="card active" style="left:463px">
    <svg class="icon" viewBox="0 0 76 76" role="img" aria-label="Wheel balancing icon" fill="none" stroke="#3F86C9" stroke-width="3"><rect x="22" y="10" width="32" height="56" rx="6"/><path d="M4 38h68"/></svg>
    <h3>Wheel Straightening and Balancing</h3>
    <p>Correct bent or misaligned wheels for improved safety, tire wear, and vehicle stability.</p>
    <div class="more">REED MORE ⟶</div>
  </div>
  <div class="card" style="left:765px">
    <svg class="icon" viewBox="0 0 76 76" role="img" aria-label="Spray paint gun icon" fill="none" stroke="#222" stroke-width="3"><rect x="26" y="16" width="34" height="18" rx="4"/><path d="M38 34v30M60 22l10-6"/></svg>
    <h3>Custom Wheel Painting and Powder Coating</h3>
    <p>Personalize wheels with custom colors and finishes, adding style and durability.</p>
    <div class="more">REED MORE ⟶</div>
  </div>
  <a class="btn">Get a free quote</a>
</section>

<section class="section mission">
  <div class="eyebrow center">Mission Statement</div>
  <h2 class="display center">Restore &amp; Improve</h2>
  <div class="point" style="left:161px">
    <div class="tick"><svg width="28" height="28" viewBox="0 0 24 24" fill="none" stroke="#fff" stroke-width="3"><path d="M4 12l5 5L20 6"/></svg></div>
    <h4>RENEW AESTHETIC APPEAL</h4>
    <p>At Kestrel Rimcare, we revive your alloy wheels' aesthetics. Scuffs, scratches, and curb damage can mar your vehicle's look. Our experts use advanced techniques to repair and refinish your wheels, restoring their shine and your car's visual appeal.</p>
  </div>
  <div class="point" style="left:620px">
    <div class="tick"><svg width="28" height="28" viewBox="0 0 24 24" fill="none" stroke="#fff" stroke-width="3"><path d="M4 12l5 5L20 6"/></svg></div>
    <h4>BOOST SAFETY &amp; PERFORMANCE</h4>
    <p>Damaged wheels affect handling and safety. We ensure your wheels meet factory standards, enhancing safety and performance for a smoother drive. Choose Kestrel Rimcare for top-quality wheel repairs.</p>
  </div>
</section>
<div class="photo mission-photo" role="img" aria-label="Photo of a technician holding an alloy wheel with tire in a workshop"></div>

<section class="gallery-head">
  <div class="eyebrow center">Gallery</div>
  <h2 class="display center">Explore our works</h2>
</section>
<div class="tile" style="left:163px;top:2389px" role="img" aria-label="Mechanic fitting a tire onto a wheel"></div>
<div class="tile" style="left:459px;top:2389px" role="img" aria-label="Alloy wheel being spray painted"></div>
<div class="tile" style="left:755px;top:2389px" role="img" aria-label="Technician at a tire changing machine"></div>
<div class="tile" style="left:163px;top:2671px" role="img" aria-label="Tire being removed from a rim on a machine"></div>
<div class="tile" style="left:459px;top:2671px" role="img" aria-label="Mechanic working on a wheel in the garage"></div>
<div class="tile" style="left:755px;top:2671px" role="img" aria-label="Gloved hands balancing a wheel"></div>
<a class="view-all">VIEW ALL ⟶</a>

<section class="section quote center">
  <div class="eyebrow">Request a Quote</div>
  <h2 class="display">Request a<br>Personalized Quote</h2>
  <div class="rule"></div>
  <p>Empower Your Decision-Making With A Detailed Quote<br>Customized To Your Unique Preferences And Requirements</p>
  <div class="btns"><a class="btn">Get a free quote</a><a class="btn outline">Know more</a></div>
</section>

<section class="section testimonials">
  <div class="eyebrow center">Testimonials</div>
  <h2 class="display center">Our customers say</h2>
  <div class="review" style="left:163px"><span class="qm">“</span><p>I was thoroughly impressed with the level of professionalism and attention to detail that Kestrel Rimcare provided. Their team not only restored my alloy wheels to perfection but also took the time to explain the entire process. The results exceeded my expectations, and I couldn't be happier with the improved aesthetics and performance of my vehicle.</p></div>
  <div class="review active" style="left:463px"><span class="qm">“</span><p>Kestrel Rimcare completely transformed the look of my car! I had some deep scratches and scuffs on my alloy wheels that were driving me crazy. Their team worked their magic and made them look brand new. From the initial inquiry to the final result, their customer service was exceptional, and the quality of their work is outstanding.</p></div>
  <div class="review" style="left:765px"><span class="qm">“</span><p>I was amazed at how quickly Kestrel Rimcare repaired my bent alloy wheel. I thought I might need to replace it, but their expert technicians had it back in shape in no time. It's great to know there's a reliable and efficient wheel repair service like theirs! They not only fixed my wheel but also took the time to explain the process.</p></div>
  <div class="who" style="left:226px"><div class="av" role="img" aria-label="Customer avatar"></div><div><b>DANA R.</b><span>★★★★★</span></div></div>
  <div class="who" style="left:526px"><div class="av" role="img" aria-label="Customer avatar"></div><div><b>LUIS P.</b><span>★★★★★</span></div></div>
  <div class="who" style="left:826px"><div class="av" role="img" aria-label="Customer avatar"></div><div><b>NORA K.</b><span>★★★★★</span></div></div>
  <div class="dots"><i></i><i class="on"></i><i></i></div>
</section>

<section class="section contact">
  <div class="photo" role="img" aria-label="Photo of a mechanic kneeling beside a wheel and tire"></div>
  <div class="eyebrow">Contact Us</div>
  <h2 class="display">Get in touch<br>with us</h2>
  <div class="field" style="left:644px;top:222px;width:200px">First Name <em>*</em></div>
  <div class="field" style="left:884px;top:222px;width:214px">Last Name <em>*</em></div>
  <div class="field" style="left:644px;top:282px;width:200px">Email Address <em>*</em></div>
  <div class="field" style="left:884px;top:282px;width:214px">Phone Number <em>*</em></div>
  <div class="field" style="left:644px;top:342px;width:454px;height:80px">How we can help you <em>*</em></div>
  <a class="btn">Submit</a>
</section>

<footer class="section footer">
  <div class="brand"><span class="dot"></span><span>Kestrel<br>Rimcare</span></div>
  <p class="about">we're dedicated to excellence in wheel repair, enhancing your vehicle's aesthetics and safety.</p>
  <div class="socials"><i></i><i></i><i></i></div>
  <div class="col" style="left:482px"><h5>USEFUL LINKS</h5><ul><li>Services</li><li>Gallery</li><li>Our Clients</li><li>Contact Us</li></ul></div>
  <div class="col" style="left:662px"><h5>SERVICES</h5><ul><li>Wheel Rim Refinishing</li><li>Wheel Straightening<br>And Balancing</li><li>Custom Wheel Painting<br>And Powder Coating</li></ul></div>
  <div class="col contact-col" style="left:884px"><h5>CONTACT US</h5><ul>
    <li><svg width="14" height="16" viewBox="0 0 24 24" fill="#3F86C9"><path d="M12 2a7 7 0 0 0-7 7c0 5 7 13 7 13s7-8 7-13a7 7 0 0 0-7-7zm0 9.5A2.5 2.5 0 1 1 12 6a2.5 2.5 0 0 1 0 5.5z"/></svg><span>418 Foundry Lane<br>Riverton, Ohio 44021</span></li>
    <li><svg width="14" height="14" viewBox="0 0 24 24" fill="#3F86C9"><path d="M5 3h4l2 5-3 2a11 11 0 0 0 6 6l2-3 5 2v4a2 2 0 0 1-2 2A17 17 0 0 1 3 5a2 2 0 0 1 2-2z"/></svg><span>(406) 555-0188</span></li>
    <li><svg width="14" height="14" viewBox="0 0 24 24" fill="#3F86C9"><path d="M2 5h20v14H2zM2 5l10 8 10-8" stroke="#16181c" stroke-width="1.5"/></svg><span>hello@kestrelrim.com</span></li>
  </ul></div>
  <div class="line"></div>
  <div class="copy center">© 2023 All Rights Reserved | Kestrel Rimcare</div>
</footer>

</body>
</html>
```